LHP Regal Business Card Design 2020

Your Manor Steward is looking for a business card that is clean and straight to the point but still looks high-end and attractive. We are a team comprised of management and field professionals focused on the high-end residential marketplace. We serve homeowners and trade professionals directly based out of the Metrowest/Boston area. We provide client services as well as construction/renovation services.
We are aiming for a black and white feel (white background and black text) and a matte finish with rounded edges.

We want to emphasis our vision of "Properties - Projects - Partners".
Dana Pellham is the president of LHP

Please include the following areas we service: Boston/Cape/Newport
Please make sure to include Dana's mobile (555) 213 4480 & office number (555) 640 1937, email dana@yourmanorsteward.example and website www.yourmanorsteward.example

Colors

Designer to choose only greyscale colors for use in the design.

Requirements
Must have
• Include "Properties - Projects - Partners" in design

Include "After Hours Emergency Support # 1800 555 0142" with icon

```html
<!DOCTYPE html>
<html lang="en">
<head>
<meta charset="utf-8">
<title>LHP Business Card</title>
<link href="https://fonts.googleapis.com/css2?family=Josefin+Sans:wght@300;400;700&display=swap" rel="stylesheet">
<style>
  :root {
    --canvas: #e6e6e6;
    --paper: #f7f7f7;
    --ink: #242424;
    --stripe: #8c8c8c;
    --light-text: #e9e9e9;
    --muted-text: #9a9a9a;
  }
  * { margin: 0; padding: 0; box-sizing: border-box; }
  html, body {
    width: 1200px; height: 801px; overflow: hidden;
    background: var(--canvas);
    font-family: "Josefin Sans", sans-serif;
  }
  .sheet {
    width: 1200px; height: 801px;
    display: flex; align-items: center; justify-content: center; gap: 40px;
  }
  .card {
    position: relative;
    width: 540px; height: 309px;
    border-radius: 12px;
    overflow: hidden;
    box-shadow: 0 4px 14px rgba(0,0,0,0.12);
  }
  .card--front { background: var(--paper); }
  .card--back { background: var(--ink); }
  .card__shape { position: absolute; inset: 0; }

  .brand {
    position: absolute;
    display: flex; flex-direction: column; align-items: center;
    font-weight: 700;
    color: var(--ink);
  }
  .brand__name { font-size: 58px; line-height: 1; letter-spacing: 1px; }
  .brand__tagline { font-size: 12px; letter-spacing: 2.5px; margin-top: 6px; text-transform: uppercase; }
  .card--front .brand { right: 28px; top: 18px; }

  .card--back .brand {
    color: var(--light-text);
    left: 50%; top: 50%; transform: translate(-50%, -50%);
  }
  .card--back .brand__name { font-size: 86px; }
  .card--back .brand__tagline { font-size: 16px; letter-spacing: 3px; margin-top: 8px; }
  .vision {
    margin-top: 14px;
    font-size: 11px; font-weight: 300; letter-spacing: 2px;
    color: var(--muted-text); text-transform: uppercase; white-space: nowrap;
  }

  .contact {
    position: absolute; left: 40px; top: 170px;
    color: var(--light-text);
  }
  .contact__name { font-size: 18px; font-weight: 400; letter-spacing: 1.5px; text-transform: uppercase; }
  .contact__role { font-size: 12px; font-weight: 300; color: var(--muted-text); margin-top: 3px; }
  .contact__list { list-style: none; margin-top: 12px; }
  .contact__item {
    display: flex; align-items: center; gap: 8px;
    font-size: 12px; font-weight: 300; letter-spacing: 0.5px; margin-top: 4px;
  }
  .contact__icon { width: 13px; height: 13px; flex: none; }

  .areas {
    position: absolute; right: 30px; top: 150px;
    font-size: 11px; font-weight: 400; letter-spacing: 1.5px;
    color: var(--muted-text); text-transform: uppercase;
  }
  .emergency {
    position: absolute; right: 30px; bottom: 52px;
    display: flex; align-items: center; gap: 8px;
    color: var(--light-text); text-align: right;
  }
  .emergency__text { font-size: 10px; font-weight: 300; letter-spacing: 0.5px; line-height: 1.4; }
  .emergency__number { font-size: 12px; font-weight: 400; letter-spacing: 0.8px; }
  .emergency__icon { width: 20px; height: 20px; flex: none; }
  .website {
    position: absolute; right: 30px; bottom: 26px;
    font-size: 12px; font-weight: 300; letter-spacing: 0.6px;
    color: var(--light-text);
  }
</style>
</head>
<body>
<main class="sheet">
  <section class="card card--front" aria-label="Business card front">
    <svg class="card__shape" viewBox="0 0 540 309" aria-hidden="true">
      <polygon points="0,192 50,124 540,92 540,106 54,140 0,210" fill="var(--stripe)"/>
      <polygon points="0,309 0,214 56,146 540,112 540,309" fill="var(--ink)"/>
    </svg>
    <div class="brand">
      <span class="brand__name">LHP</span>
      <span class="brand__tagline">Your Manor Steward</span>
    </div>
    <div class="contact">
      <p class="contact__name">Dana Pellham</p>
      <p class="contact__role">President of LHP</p>
      <ul class="contact__list">
        <li class="contact__item">
          <svg class="contact__icon" viewBox="0 0 14 14" aria-label="Office"><circle cx="7" cy="7" r="7" fill="var(--muted-text)"/><path d="M4 5.5h6v4H4z" fill="var(--ink)"/></svg>
          (555) 640 1937
        </li>
        <li class="contact__item">
          <svg class="contact__icon" viewBox="0 0 14 14" aria-label="Mobile"><circle cx="7" cy="7" r="7" fill="var(--muted-text)"/><rect x="5" y="3.5" width="4" height="7" rx="0.8" fill="var(--ink)"/></svg>
          (555) 213 4480
        </li>
        <li class="contact__item">
          <svg class="contact__icon" viewBox="0 0 14 14" aria-label="Email"><circle cx="7" cy="7" r="7" fill="var(--muted-text)"/><rect x="3.5" y="4.5" width="7" height="5" fill="var(--ink)"/><path d="M3.5 4.5l3.5 3 3.5-3" stroke="var(--muted-text)" stroke-width="0.8" fill="none"/></svg>
          dana@yourmanorsteward.example
        </li>
      </ul>
    </div>
    <p class="areas">Boston / Cape / Newport</p>
    <div class="emergency">
      <div>
        <p class="emergency__text">After Hours Emergency Support</p>
        <p class="emergency__number"># 1800 555 0142</p>
      </div>
      <svg class="emergency__icon" viewBox="0 0 20 20" aria-label="Emergency phone">
        <circle cx="10" cy="10" r="10" fill="var(--muted-text)"/>
        <path d="M6.5 5.5c.6-.6 1.4-.5 1.8.1l.9 1.4c.3.5.2 1.1-.2 1.4l-.6.5c.6 1.3 1.6 2.3 2.9 2.9l.5-.6c.3-.4.9-.5 1.4-.2l1.4.9c.6.4.7 1.2.1 1.8l-.6.6c-.8.8-2.3.8-4-.3-1.6-1-3-2.4-4-4-1.1-1.7-1.1-3.2-.3-4z" fill="var(--ink)"/>
      </svg>
    </div>
    <p class="website">www.yourmanorsteward.example</p>
  </section>

  <section class="card card--back" aria-label="Business card back">
    <div class="brand">
      <span class="brand__name">LHP</span>
      <span class="brand__tagline">Your Manor Steward</span>
      <span class="vision">Properties - Projects - Partners</span>
    </div>
  </section>
</main>
</body>
</html>
```